Card Design for my dog training business Brightpaw Obedience

Need a business card design for my dog training business with my new logo. Want the card to come off professional yet fun. Want it to be very eye catchy as well. I normally have these at vet clinics, pet stores, and groomers. so need it to look better than my competitors.
Target Market(s)
dog owners
Industry/Entity Type
Dog Training
Contact Information for Business Card
needs logo, my name and info
Font styles to use
Serif
Colors
0255a3
ffffff
ec1f27
000000
333333
fbfbfb
Requirements
Must have
- Brightpaw Obedience
- Felix Orland
- 415 903 2276
- info@brightpawobedience.example
- www.brightpawobedience.example

```html
<!DOCTYPE html>
<html lang="en">
<head>
<meta charset="utf-8">
<title>Brightpaw Obedience – Business Card</title>
<link href="https://fonts.googleapis.com/css2?family=Cinzel:wght@400;600&family=EB+Garamond:ital,wght@0,400;1,400&display=swap" rel="stylesheet">
<style>
  :root {
    --red: #ec1f27;
    --red-deep: #d91a22;
    --blue: #0255a3;
    --white: #ffffff;
    --paper: #fbfbfb;
    --ink: #000000;
    --text: #333333;
    --stage: #1c1c1c;
  }
  * { box-sizing: border-box; margin: 0; padding: 0; }
  html, body { width: 1200px; height: 1200px; overflow: hidden; }
  body {
    background: var(--stage);
    display: flex;
    flex-direction: column;
    align-items: center;
    justify-content: center;
    gap: 40px;
    font-family: "EB Garamond", Georgia, serif;
  }
  .card {
    position: relative;
    width: 900px;
    height: 514px;
    border-radius: 22px;
    overflow: hidden;
  }

  /* ---------- Front ---------- */
  .card--front { color: var(--white); }
  .card--front .pattern {
    position: absolute; inset: 0;
    background: radial-gradient(ellipse at center, var(--red) 0%, var(--red-deep) 100%);
  }
  .front-brand {
    position: absolute; inset: 0;
    display: flex; flex-direction: column; align-items: center; justify-content: center;
    gap: 26px;
  }
  .brand-lockup { display: flex; align-items: center; gap: 18px; }
  .brand-dot {
    flex: none;
    width: 34px; height: 34px; border-radius: 50%;
    background: currentColor;
  }
  .brand-name {
    font-family: "Cinzel", Georgia, serif;
    font-weight: 400;
    font-size: 58px;
    letter-spacing: 2px;
    line-height: 1;
  }
  .tagline {
    font-style: italic;
    font-size: 22px;
    letter-spacing: .3px;
  }

  /* ---------- Back ---------- */
  .card--back { background: var(--paper); color: var(--text); }
  .card--back .pattern {
    position: absolute; inset: 0;
    background: linear-gradient(135deg, #f4f4f4 0%, var(--paper) 50%, #f2f2f2 100%);
  }
  .back-brand {
    position: absolute; left: 40px; top: 150px; width: 400px;
    color: var(--ink);
  }
  .back-brand .brand-name { font-size: 38px; }
  .back-brand .brand-dot { width: 24px; height: 24px; }
  .divider {
    position: absolute; left: 468px; top: 60px;
    width: 1.5px; height: 300px; background: var(--text);
  }
  .contact {
    position: absolute; left: 505px; top: 92px;
  }
  .contact-name {
    font-family: "Cinzel", Georgia, serif;
    font-size: 34px; font-weight: 400; color: var(--ink);
    letter-spacing: 1.5px;
    margin-bottom: 20px;
  }
  .contact-list { list-style: none; display: flex; flex-direction: column; gap: 14px; }
  .contact-item { display: flex; align-items: center; gap: 16px; font-size: 23px; color: var(--ink); }
  .contact-icon {
    width: 42px; height: 42px; border-radius: 50%;
    border: 2px solid var(--red);
    display: flex; align-items: center; justify-content: center;
    flex: none;
  }
  .contact-icon svg { width: 24px; height: 24px; }

  .swoosh { position: absolute; inset: 0; width: 100%; height: 100%; }
  .places {
    position: absolute; right: 40px; bottom: 14px;
    display: flex; align-items: center; gap: 12px;
    font-family: "Cinzel", Georgia, serif;
    font-size: 21px; color: var(--white); letter-spacing: 1px;
  }
  .paw { width: 22px; height: 22px; flex: none; }
</style>
</head>
<body>

  <!-- Front of card -->
  <section class="card card--front">
    <div class="pattern" role="img" aria-label="Faint red pattern of pet icons: bones, paws, dog houses, bowls and grooming tools"></div>
    <div class="front-brand">
      <div class="brand-lockup">
        <span class="brand-dot"></span>
        <span class="brand-name">Brightpaw Obedience</span>
      </div>
      <p class="tagline">“Patient, positive training for every dog we meet.”</p>
    </div>
  </section>

  <!-- Back of card -->
  <section class="card card--back">
    <div class="pattern" role="img" aria-label="Faint grey pattern of pet icons: bones, paws, dog houses, bowls and grooming tools"></div>

    <svg class="swoosh" viewBox="0 0 900 514" preserveAspectRatio="none" aria-hidden="true">
      <path d="M0,340 C220,344 430,368 640,415 C430,382 220,366 0,366 Z" fill="var(--blue)"/>
      <path d="M0,380 C300,388 620,420 900,456 L900,514 L0,514 Z" fill="var(--red)"/>
    </svg>

    <div class="back-brand brand-lockup">
      <span class="brand-dot"></span>
      <span class="brand-name">Brightpaw Obedience</span>
    </div>

    <div class="divider"></div>

    <div class="contact">
      <h1 class="contact-name">Felix Orland</h1>
      <ul class="contact-list">
        <li class="contact-item">
          <span class="contact-icon">
            <svg viewBox="0 0 24 24"><path d="M6.6 3.5l3 3.2-1.8 2.2c1.2 2.6 3.2 4.6 5.8 5.8l2.2-1.8 3.2 3-1.8 3c-7.6-.4-13.8-6.6-14.2-14.2z" fill="none" stroke="var(--red)" stroke-width="1.8" stroke-linejoin="round"/></svg>
          </span>
          415 903 2276
        </li>
        <li class="contact-item">
          <span class="contact-icon">
            <svg viewBox="0 0 24 24"><rect x="3" y="6" width="18" height="12" rx="1.5" fill="var(--red)"/><path d="M3.5 6.5l8.5 7 8.5-7" fill="none" stroke="var(--white)" stroke-width="1.5"/></svg>
          </span>
          info@brightpawobedience.example
        </li>
        <li class="contact-item">
          <span class="contact-icon">
            <svg viewBox="0 0 24 24" fill="none" stroke="var(--red)" stroke-width="1.6"><circle cx="12" cy="12" r="9"/><ellipse cx="12" cy="12" rx="4" ry="9"/><path d="M3 12h18M4.5 7.5h15M4.5 16.5h15"/></svg>
          </span>
          www.brightpawobedience.example
        </li>
      </ul>
    </div>

    <p class="places">
      <svg class="paw" viewBox="0 0 24 24" fill="var(--white)"><ellipse cx="12" cy="16" rx="5" ry="4.5"/><circle cx="5" cy="10" r="2.2"/><circle cx="9" cy="5.5" r="2.2"/><circle cx="15" cy="5.5" r="2.2"/><circle cx="19" cy="10" r="2.2"/></svg>
      Vet Clinics
      <svg class="paw" viewBox="0 0 24 24" fill="var(--white)"><ellipse cx="12" cy="16" rx="5" ry="4.5"/><circle cx="5" cy="10" r="2.2"/><circle cx="9" cy="5.5" r="2.2"/><circle cx="15" cy="5.5" r="2.2"/><circle cx="19" cy="10" r="2.2"/></svg>
      Pet Stores
      <svg class="paw" viewBox="0 0 24 24" fill="var(--white)"><ellipse cx="12" cy="16" rx="5" ry="4.5"/><circle cx="5" cy="10" r="2.2"/><circle cx="9" cy="5.5" r="2.2"/><circle cx="15" cy="5.5" r="2.2"/><circle cx="19" cy="10" r="2.2"/></svg>
      Groomers.
    </p>
  </section>

</body>
</html>
```